Kestrel Motion LLC Sports Therapy and Soft Tissue Injury solutions

We are a company that specializes in Sports Therapy, Physical therapy, muscular rehab, nutrition plans, and personal training. Kestrel Motion travels around the country and world treating athletes and people in the workforce that have Soft Tissue injuries. We are legally partnered with VMR(Vantor Muscle Recovery/vantorrecovery.example) in treating endurance athletes ex. SteelRidge triathalon. We educate our patients on how to sustain a healthy lifestyle.We need a web design that has a Home page summarizing our services, a Physical therapy page, a Personal training and nutrition page. Our ultimate goal is to build relationships with fitness centers, training facilities, and companies that are implementing preventative health measures for their employees. We want to incorporate the VMR logo and Steelridge logo attached in the website but, we want to use our own name (Kestrel Motion LLC) as the main draw. We will provide literature for the website.

Target Market(s)

Grindlane training gyms, Fitness centers, Dance studios, Companies looking for Corporate Wellness programs

Industry/Entity Type

Health And Wellness

Number of Pages Required

4 page

Font styles to use
Sans Serif

Requirements
Must have
• Stock Photos of Athletes training. Examples of Endurance Athletes and Cross training. A mesh of as many sports and training methods as possible. We are a new company and don't have many photos. Easy accessibility to change and add text as the company grows. Vantor Muscle recovery logo incorporated in the back ground of the website. Always visible but does not take over the web page
Nice to have
• Sleek and cool, and masculine design. We want the website to stand out without focusing on one individual. We want to use the website to brand the company (Kestrel Motion LLC) with easy access to social media platforms

```html
<!DOCTYPE html>
<html lang="en">
<head>
<meta charset="utf-8">
<title>Kestrel Motion LLC — Sports Therapy</title>
<link rel="stylesheet" href="https://fonts.googleapis.com/css2?family=Oswald:wght@400;500&family=Open+Sans:wght@400;600;700&family=Roboto:wght@400;500&display=swap">
<style>
:root{
  --red:#c8161d;
  --red-dark:#a50f15;
  --ink:#222;
  --text:#555;
  --muted:#777;
  --dark:#151515;
  --band:#1d1d1d;
  --light:#e9e9e9;
  --white:#fff;
  --footer:#f4f4f4;
  --bar:#e3e3e3;
}
*{box-sizing:border-box;margin:0;padding:0}
html,body{width:1200px;height:2885px;overflow:hidden}
body{position:relative;background:var(--white);font-family:"Open Sans",Arial,sans-serif;color:var(--ink)}
.abs{position:absolute}
.heading{font-family:"Oswald",Arial,sans-serif;font-weight:500}

/* header */
.site-header{position:absolute;left:0;top:0;width:1200px;height:115px;background:var(--white)}
.brand{left:100px;top:36px;display:flex;align-items:center;gap:14px}
.brand-dot{width:38px;height:38px;border-radius:50%;background:var(--red)}
.brand-name{font-family:"Oswald",sans-serif;font-weight:500;font-size:30px;color:var(--red)}
.top-contacts{right:72px;top:14px;display:flex;gap:24px;font-size:15px}
.top-contact{display:flex;align-items:center;gap:10px}
.top-contact .ic{width:32px;height:32px;border-radius:50%;display:flex;align-items:center;justify-content:center}
.ic-red{background:var(--red)}
.ic-dark{background:#333}
.main-nav{right:46px;top:68px;display:flex;gap:38px;font-size:16px;font-weight:600}
.main-nav a{color:var(--ink);text-decoration:none}
.main-nav a.active{color:var(--red)}

/* hero */
.hero{left:0;top:115px;width:1200px;height:514px;background:linear-gradient(90deg,#d9d4cf 0%,#c9c1ba 35%,#b9a9a3 60%,#d8a890 85%,#e6c2a0 100%)}
.hero-title{left:98px;top:106px;font-size:50px;color:var(--red);font-family:"Oswald",sans-serif;font-weight:500}
.hero-text{left:100px;top:196px;width:480px;font-size:15px;line-height:25px;color:#333;font-family:"Roboto",sans-serif}
.btn-red{display:flex;align-items:center;justify-content:center;background:var(--red);color:var(--white);font-weight:600;text-decoration:none}
.hero-btn{left:100px;top:287px;width:137px;height:48px;border-radius:24px;font-size:16px}
.hero-dots{left:100px;top:376px;display:flex;gap:6px}
.hero-dots span{width:14px;height:14px;border-radius:50%;border:2px solid #333;background:transparent}
.hero-dots span.on{background:var(--red);border-color:var(--red)}

/* intro */
.section-title{width:1200px;left:0;text-align:center;font-family:"Oswald",sans-serif;font-weight:500;font-size:31px}
.section-title::after{content:"";display:block;width:120px;height:2px;background:var(--red);margin:14px auto 0}
.intro-title{top:710px;color:var(--red)}
.intro-text{left:140px;top:792px;width:920px;text-align:center;font-size:12.5px;line-height:22px;color:var(--text);font-family:"Roboto",sans-serif}
.focus-card{width:258px;height:258px;border-radius:50%;border:3px solid #222;padding:6px;top:892px}
.focus-card.red{border-color:var(--red)}
.focus-photo{width:100%;height:100%;border-radius:50%;position:relative;overflow:hidden}
.focus-label{position:absolute;left:0;right:0;bottom:0;height:68px;display:flex;align-items:flex-start;justify-content:center;padding-top:12px;color:var(--white);font-size:25px;font-weight:600;letter-spacing:.5px}
.focus-card.red .focus-label{background:rgba(200,22,29,.85);height:100px;padding-top:14px}
.focus-card.dark .focus-label{background:rgba(30,30,30,.75)}

/* services */
.services{left:0;top:1196px;width:1200px;height:656px}
.services-title{top:1310px;color:var(--white);font-size:30px}
.services-title::after{background:var(--white)}
.service{top:1436px;width:200px;text-align:center;color:var(--white)}
.service-icon{width:138px;height:138px;margin:0 auto;border-radius:50%;border:3px solid var(--white);background:var(--dark);display:flex;align-items:center;justify-content:center;position:relative}
.service-icon::after{content:"";position:absolute;bottom:-13px;left:50%;margin-left:-12px;border-left:12px solid transparent;border-right:12px solid transparent;border-top:13px solid var(--white)}
.service-icon.red{background:var(--red)}
.service-name{margin-top:40px;font-size:20px;font-family:"Roboto",sans-serif;font-weight:500}
.service-text{margin-top:14px;font-size:12px;line-height:20px;font-family:"Roboto",sans-serif;padding:0 8px}

/* news */
.news{left:0;top:1846px;width:1200px;height:644px;background:var(--light)}
.news-title{top:1876px;color:var(--red)}
.post{top:1971px;width:317px}
.post-photo{width:317px;height:244px;position:relative}
.post-date{position:absolute;left:0;bottom:0;width:55px;height:66px;background:#1a1a1a;color:var(--white);font-size:16px;font-weight:600;text-align:center;line-height:24px;padding-top:8px}
.post-date.red{background:var(--red)}
.post-title{margin-top:24px;text-align:center;font-size:19px;font-family:"Roboto",sans-serif;color:#222}
.post-text{margin-top:12px;text-align:center;font-size:13px;line-height:24px;color:var(--muted);font-family:"Roboto",sans-serif}
.post-btn{margin:22px auto 0;width:108px;height:40px;font-size:14px;display:flex;align-items:center;justify-content:center;font-weight:600;text-decoration:none}
.post-btn.outline{border:2px solid #333;color:#222;background:var(--white)}

/* footer */
.site-footer{left:0;top:2490px;width:1200px;height:333px;background:var(--footer);border-top:4px solid var(--red)}
.footer-map{left:0;top:2494px;width:1200px;height:329px;background:linear-gradient(100deg,#efefef,#f7f7f7 40%,#ececec)}
.partner{left:104px;width:170px;height:40px;background:#d9d9d9;border-radius:4px}
.foot-head{font-size:18px;font-weight:700;color:var(--red);font-family:"Roboto",sans-serif;letter-spacing:.3px}
.foot-head::after{content:"";display:block;width:104px;height:2px;background:var(--red);margin-top:12px}
.quick-links{left:333px;top:2536px}
.quick-links ul{list-style:none;margin-top:20px}
.quick-links li{font-size:14px;line-height:32px;color:#333;font-family:"Roboto",sans-serif}
.contact{left:527px;top:2536px}
.contact-row{display:flex;gap:16px;margin-top:24px}
.contact-row:first-of-type{margin-top:22px}
.contact-ic{width:38px;height:38px;border-radius:50%;border:2px solid var(--red);display:flex;align-items:center;justify-content:center;flex:none;background:var(--white)}
.contact-label{font-size:14px;font-weight:600;color:#222}
.contact-val{font-size:12.5px;line-height:20px;color:#444;font-family:"Roboto",sans-serif}
.contact-form{left:813px;top:2536px;width:290px}
.field{position:absolute;background:var(--white);border:1px solid #bbb;font-size:11px;color:#666;padding:6px 10px;font-family:"Roboto",sans-serif}
.send-btn{position:absolute;left:0;top:179px;width:119px;height:37px;font-size:12px}

.copy-bar{left:0;top:2823px;width:1200px;height:62px;background:var(--bar)}
.copyright{left:100px;top:2843px;font-size:15px;color:#222;font-family:"Roboto",sans-serif}
.socials{left:872px;top:2833px;display:flex;gap:12px}
.socials span{width:38px;height:38px;border-radius:50%;border:2px solid #333}
</style>
</head>
<body>

<header class="site-header">
  <div class="abs brand">
    <span class="brand-dot"></span>
    <span class="brand-name">Kestrel Motion LLC</span>
  </div>
  <div class="abs top-contacts">
    <div class="top-contact">
      <span class="ic ic-red"><svg width="16" height="12" viewBox="0 0 16 12"><rect x="0.5" y="0.5" width="15" height="11" fill="none" stroke="#fff"/><path d="M1 1l7 6 7-6" fill="none" stroke="#fff"/></svg></span>
      <span style="color:var(--red)">info@kestrelmotion.example</span>
    </div>
    <div class="top-contact">
      <span class="ic ic-dark"><svg width="14" height="14" viewBox="0 0 24 24"><path d="M6.6 10.8a15 15 0 006.6 6.6l2.2-2.2a1 1 0 011-.25 11.4 11.4 0 003.6.6 1 1 0 011 1V20a1 1 0 01-1 1A17 17 0 013 4a1 1 0 011-1h3.5a1 1 0 011 1c0 1.25.2 2.45.6 3.6a1 1 0 01-.25 1z" fill="#fff"/></svg></span>
      <span>(555)014-2290</span>
    </div>
  </div>
  <nav class="abs main-nav">
    <a class="active" href="#">Home</a>
    <a href="#">Services</a>
    <a href="#">Physical Therapy</a>
    <a href="#">Personal Training</a>
    <a href="#">Nutrition</a>
    <a href="#">Contact</a>
  </nav>
</header>

<section class="abs hero" role="img" aria-label="Photo of a woman running on a bridge at sunset">
  <h1 class="abs hero-title">Kestrel Motion LLC</h1>
  <p class="abs hero-text">Kestrel Motion travels around the country and world treating athletes and people in the workforce that have Soft Tissue injuries.</p>
  <a class="abs btn-red hero-btn" href="#">Read More</a>
  <div class="abs hero-dots"><span class="on"></span><span></span><span></span><span></span><span></span></div>
</section>

<h2 class="abs section-title intro-title">Kestrel Motion LLC</h2>
<p class="abs intro-text">Kestrel Motion travels around the country and world treating athletes and people in the workforce that have Soft Tissue injuries. We are a company that specializes in Sports Therapy, Physical therapy, muscular rehab, nutrition plans, and personal training.</p>

<div class="abs focus-card red" style="left:177px">
  <div class="focus-photo" role="img" aria-label="Photo of an athlete running on a red stadium track" style="background:linear-gradient(180deg,#dfe3d6 0%,#c9cbb9 40%,#b8332f 60%,#a4161a 100%)">
    <div class="focus-label">SPORTS</div>
  </div>
</div>
<div class="abs focus-card dark" style="left:469px">
  <div class="focus-photo" role="img" aria-label="Photo of a man doing push-ups" style="background:linear-gradient(160deg,#d8d8d8 0%,#9a9a9a 45%,#4a4038 100%)">
    <div class="focus-label">PHYSICAL</div>
  </div>
</div>
<div class="abs focus-card dark" style="left:761px">
  <div class="focus-photo" role="img" aria-label="Photo of a woman training with a medicine ball" style="background:linear-gradient(160deg,#c9c9c4 0%,#8d8a86 45%,#3e3e3e 100%)">
    <div class="focus-label">MUSCULAR</div>
  </div>
</div>

<svg class="abs services" viewBox="0 0 1200 656" role="img" aria-label="Dark background photo of people working out in a gym">
  <defs>
    <linearGradient id="bandShade" x1="0" y1="0" x2="1" y2="1">
      <stop offset="0" stop-color="#1b1b1b"/>
      <stop offset=".5" stop-color="#262626"/>
      <stop offset="1" stop-color="#161616"/>
    </linearGradient>
  </defs>
  <polygon points="0,6 600,50 1200,6 1200,650 600,612 0,650" fill="url(#bandShade)"/>
</svg>

<h2 class="abs section-title services-title">Kestrel Motion LLC Services</h2>

<div class="abs service" style="left:85px">
  <div class="service-icon">
    <svg width="64" height="64" viewBox="0 0 64 64" fill="none" stroke="#fff" stroke-width="4" stroke-linecap="round" stroke-linejoin="round">
      <circle cx="40" cy="12" r="5" fill="#fff" stroke="none"/>
      <path d="M24 24l12-4 6 10 10 2"/><path d="M36 20l-6 16 10 8-2 14"/><path d="M30 36l-6 10H12"/>
      <path d="M4 26h12M2 34h10M6 42h8"/>
    </svg>
  </div>
  <div class="service-name">Sports Therapy</div>
  <p class="service-text">We are a company that specializes in Sports Therapy, Physical therapy.</p>
</div>
<div class="abs service" style="left:294px">
  <div class="service-icon red">
    <svg width="64" height="64" viewBox="0 0 64 64" fill="none" stroke="#fff" stroke-width="4" stroke-linecap="round">
      <circle cx="22" cy="14" r="6" fill="#fff" stroke="none"/>
      <circle cx="38" cy="40" r="16" fill="#fff" stroke="none"/>
      <path d="M14 24l8 10 6-4"/><path d="M10 34l4 18"/>
    </svg>
  </div>
  <div class="service-name">Physical Therapy</div>
  <p class="service-text">We are a company that specializes in Sports Therapy, Physical therapy.</p>
</div>
<div class="abs service" style="left:502px">
  <div class="service-icon">
    <svg width="68" height="64" viewBox="0 0 68 64" fill="none" stroke="#fff" stroke-width="4" stroke-linecap="round">
      <path d="M6 14h56"/><rect x="4" y="6" width="6" height="16" fill="#fff"/><rect x="58" y="6" width="6" height="16" fill="#fff"/>
      <circle cx="34" cy="28" r="5" fill="#fff" stroke="none"/>
      <path d="M22 14l6 10h12l6-10"/><path d="M28 34v14l-6 10M40 34v14l6 10"/>
    </svg>
  </div>
  <div class="service-name">Muscular Rehab</div>
  <p class="service-text">We are a company that specializes in Sports Therapy, Physical therapy.</p>
</div>
<div class="abs service" style="left:711px">
  <div class="service-icon">
    <svg width="56" height="64" viewBox="0 0 56 64" fill="none" stroke="#fff" stroke-width="4" stroke-linejoin="round" stroke-linecap="round">
      <rect x="6" y="8" width="44" height="52" rx="6"/><rect x="18" y="3" width="20" height="10" rx="3" fill="#fff"/>
      <path d="M16 26h24M16 36h24M16 46h16"/>
    </svg>
  </div>
  <div class="service-name">Nutrition Plans</div>
  <p class="service-text">We are a company that specializes in Sports Therapy, Physical therapy.</p>
</div>
<div class="abs service" style="left:913px">
  <div class="service-icon">
    <svg width="64" height="64" viewBox="0 0 64 64" fill="none" stroke="#fff" stroke-width="4" stroke-linecap="round">
      <path d="M20 4v16M44 4v16"/><circle cx="20" cy="40" r="14"/><circle cx="44" cy="40" r="14"/>
      <path d="M14 20h12M38 20h12"/>
    </svg>
  </div>
  <div class="service-name">Personal Training</div>
  <p class="service-text">We are a company that specializes in Sports Therapy, Physical therapy.</p>
</div>

<section class="abs news" aria-label="Latest news"></section>
<h2 class="abs section-title news-title">Our Latest News</h2>

<article class="abs post" style="left:100px">
  <div class="post-photo" role="img" aria-label="Photo of a group workout class with kettlebells" style="background:linear-gradient(135deg,#b9a79a 0%,#8c7b70 45%,#4a4440 100%)">
    <div class="post-date red">AUG<br>20</div>
  </div>
  <h3 class="post-title">Personal Training</h3>
  <p class="post-text">We build relationships with companies committed to the sustainable health of their employees and patrons.</p>
  <a class="post-btn btn-red" href="#">Learn More</a>
</article>
<article class="abs post" style="left:442px">
  <div class="post-photo" role="img" aria-label="Photo of a man lifting a kettlebell in a gym" style="background:linear-gradient(135deg,#6d6d6d 0%,#3d3d3d 50%,#8a8a8a 100%)">
    <div class="post-date">AUG<br>20</div>
  </div>
  <h3 class="post-title">Physical Therapy</h3>
  <p class="post-text">We build relationships with companies committed to the sustainable health of their employees and patrons.</p>
  <a class="post-btn outline" href="#">Learn More</a>
</article>
<article class="abs post" style="left:785px">
  <div class="post-photo" role="img" aria-label="Photo of a woman lifting a barbell" style="background:linear-gradient(135deg,#8e8e8e 0%,#5a5a5a 50%,#2e2e2e 100%)">
    <div class="post-date">AUG<br>20</div>
  </div>
  <h3 class="post-title">Nutrition Plans</h3>
  <p class="post-text">We build relationships with companies committed to the sustainable health of their employees and patrons.</p>
  <a class="post-btn outline" href="#">Learn More</a>
</article>

<footer class="abs site-footer"></footer>
<div class="abs footer-map" role="img" aria-label="Faint world map background"></div>

<div class="abs partner" style="top:2608px" role="img" aria-label="VMR partner badge"></div>
<div class="abs partner" style="top:2686px" role="img" aria-label="SteelRidge partner badge"></div>

<div class="abs quick-links">
  <div class="foot-head">QUICK LINKS</div>
  <ul>
    <li>› Home</li><li>› Services</li><li>› Physical Therapy</li><li>› Personal Training</li><li>› Nutrition</li><li>› Contact Us</li>
  </ul>
</div>

<div class="abs contact">
  <div class="foot-head">CONTACT US</div>
  <div class="contact-row">
    <span class="contact-ic"><svg width="14" height="18" viewBox="0 0 14 18"><path d="M7 0a7 7 0 017 7c0 5-7 11-7 11S0 12 0 7a7 7 0 017-7z" fill="#c8161d"/><circle cx="7" cy="7" r="2.5" fill="#fff"/></svg></span>
    <div><div class="contact-label">ADDRESS,</div><div class="contact-val">482 Harbor Crest Ave Suite 210<br>Lakeview, California, 90000</div></div>
  </div>
  <div class="contact-row">
    <span class="contact-ic"><svg width="12" height="18" viewBox="0 0 12 18"><rect x="1" y="1" width="10" height="16" rx="2" fill="none" stroke="#c8161d" stroke-width="2"/><circle cx="6" cy="14" r="1" fill="#c8161d"/></svg></span>
    <div><div class="contact-label">PHONE:</div><div class="contact-val">(555)014-2290</div></div>
  </div>
  <div class="contact-row">
    <span class="contact-ic"><svg width="16" height="12" viewBox="0 0 16 12"><rect width="16" height="12" rx="1" fill="#c8161d"/><path d="M1 1l7 6 7-6" fill="none" stroke="#fff" stroke-width="1.4"/></svg></span>
    <div><div class="contact-label">Mail:</div><div class="contact-val">info@kestrelmotion.example</div></div>
  </div>
</div>

<form class="abs contact-form">
  <div class="foot-head">CONTACT FORM</div>
  <div class="field" style="left:0;top:54px;width:137px;height:37px">Name</div>
  <div class="field" style="left:149px;top:54px;width:136px;height:37px">Phone</div>
  <div class="field" style="left:0;top:98px;width:285px;height:64px">Message</div>
  <div class="send-btn btn-red">SEND MESSAGE</div>
</form>

<div class="abs copy-bar"></div>
<p class="abs copyright">Copyright © 2017 Kestrel Motion LLC. All Right Reserved</p>
<div class="abs socials" aria-label="Social media links">
  <span></span><span></span><span></span><span></span><span></span>
</div>

</body>
</html>
```